Company Brochure and Presentation

Hello,

We are software development company and would like to design our company brochure (Both in high resolution Printable Format and PDF) and presentation (PPT).

The contents are ready for both assignment. Just need to align with creative design.

Please submit your portfolio so that we can short list and send you the contents.

Also, please include cost and time-frame.

Few more details for best quotation...

The company profile will have around 15 pages
The presentation (PPT) will also have 15 pages.

However, I am open for your suggestion to make it more professional designed, include more images and with less pages.

The files are attached herewith.

The rough images/ ideas for outsourcing models are provided in word file. Open for your ideas here.

Please review and let me know your best quote.

Also, please read below link before you quote so you can make a competitive bid.

http://www.pitchvale.example/quote-pitchvale.aspx?briefid=48203

Thanks & Best Regards,

Ramesh Kothari
Skype - ramesh.k.kothari
Updates

Hello All,

I hove uploaded few images like logo, banner etc. You can use those image or take as a reference. 

Also, please visit our website - www.zelvonix.example 

Thank you.

Target Market(s)

1. IT Department of the companies
2. Outsourcing IT companies
3. IT consultant

Industry/Entity Type

Software

```html
<!DOCTYPE html>
<html lang="en">
<head>
<meta charset="utf-8">
<title>Zelvonix Software Solution LLP – Brochure Cover</title>
<link rel="stylesheet" href="https://fonts.googleapis.com/css2?family=Open+Sans:wght@400;600&display=swap">
<style>
  :root {
    --stage: #e9e9e7;
    --paper: #ffffff;
    --paper-shade: #f4f4f4;
    --band-light: #e6e6e6;
    --green: #6cbd2e;
    --green-dark: #4f9a1c;
    --ink: #1d1d1d;
    --ink-soft: #6a6a6a;
    --photo-dark: #3a3a3a;
    --photo-mid: #8a8a8a;
    --curve: #dcdcdc;
  }
  * { box-sizing: border-box; margin: 0; padding: 0; }
  html, body { width: 1200px; height: 750px; overflow: hidden; }
  body {
    background: var(--stage);
    font-family: "Open Sans", Arial, sans-serif;
    position: relative;
  }
  .spread {
    position: absolute;
    left: 50px; top: 125px;
    width: 1100px; height: 500px;
    background: linear-gradient(180deg, var(--paper) 0%, var(--paper-shade) 100%);
    box-shadow: 0 6px 18px rgba(0,0,0,.18);
  }
  .spread__fold {
    position: absolute; left: 550px; top: 0;
    width: 1px; height: 100%;
    background: #e2e2e2;
  }
  .spread__shapes { position: absolute; inset: 0; }
  .band-light {
    position: absolute; left: 0; top: 200px;
    width: 550px; height: 150px;
    background: linear-gradient(90deg, #ececec 0%, var(--band-light) 100%);
  }
  .world-map {
    position: absolute; left: 290px; top: 222px;
    width: 230px; height: 112px;
    background: radial-gradient(ellipse at 50% 45%, #c9c9c9 0%, #dedede 60%, var(--band-light) 100%);
    border-radius: 30px;
  }
  .web-photo {
    position: absolute; left: 551px; top: 190px;
    width: 549px; height: 160px;
    background: linear-gradient(90deg, var(--photo-mid) 0%, var(--photo-dark) 45%, #5c5c5c 75%, #2f2f2f 100%);
  }
  .brand {
    position: absolute;
    display: flex; align-items: center; gap: 8px;
    color: var(--ink);
    font-weight: 600;
  }
  .brand__mark {
    width: 14px; height: 14px;
    background: var(--green);
  }
  .brand__name { font-size: 22px; letter-spacing: .2px; }
  .brand__suffix { font-size: 10px; font-weight: 600; margin-left: 2px; align-self: flex-end; padding-bottom: 5px; }
  .brand--back { left: 40px; top: 222px; }
  .brand--front { right: 40px; top: 48px; }
  .address {
    position: absolute; left: 62px; top: 262px;
    font-size: 11px; line-height: 15px;
    color: var(--ink-soft);
  }
</style>
</head>
<body>
  <main class="spread">
    <svg class="spread__shapes" width="1100" height="500" viewBox="0 0 1100 500" aria-hidden="true">
      <g fill="none" stroke="var(--curve)" stroke-width="1">
        <path d="M180 0 Q320 120 550 130"/>
        <path d="M260 0 Q380 100 550 110"/>
        <path d="M0 420 Q200 380 330 500"/>
        <path d="M650 0 Q760 120 1100 150"/>
        <path d="M740 500 Q820 400 1100 390"/>
        <path d="M380 500 Q460 420 550 420"/>
      </g>
    </svg>

    <div class="band-light"></div>
    <div class="world-map" role="img" aria-label="Dotted world map"></div>
    <div class="web-photo" role="img" aria-label="Close-up photo of a web address bar in greyscale with binary digits"></div>

    <svg class="spread__shapes" width="1100" height="500" viewBox="0 0 1100 500" aria-hidden="true">
      <polygon points="200,172 560,186 560,200 220,200" fill="var(--green)"/>
      <polygon points="551,176 930,176 900,190 551,190" fill="var(--green)"/>
      <polygon points="0,350 310,350 290,378 0,362" fill="var(--green)"/>
      <polygon points="740,350 1100,350 1100,380 790,362" fill="var(--green)"/>
    </svg>

    <div class="spread__fold"></div>

    <div class="brand brand--back">
      <span class="brand__mark"></span>
      <span class="brand__name">Zelvonix</span>
      <span class="brand__suffix">Software Solution LLP</span>
    </div>
    <p class="address">
      Zelvonix Software Solution LLP<br>
      14, Lakeview Park, Ring Road<br>
      Navapur-390 120, GUJARAT, INDIA
    </p>

    <div class="brand brand--front">
      <span class="brand__mark"></span>
      <span class="brand__name">Zelvonix</span>
      <span class="brand__suffix">Software Solution LLP</span>
    </div>
  </main>
</body>
</html>
```